Pebble Hop - mobile play centre poster designs

Who are we - we are a mobile playground business that specialises in providing entertainment to children in a safe, clean environment either at home or in a function centre. Brief - create 4 different signs to be displayed on our playgrounds. Please find attached 3 photos from our competitors to use as a guide. Corflute sign - size A1 Toddler zone - size A1 Playground rules - size A4 No climbing - size 20cmx8cm sending through photos and documents now.
Colors
Designer to choose colors to be used in the design.
Requirements
Must have
- Colour, be very specific with the rules, pictures

```html
<!DOCTYPE html>
<html lang="en">
<head>
<meta charset="utf-8">
<title>Pebble Hop – Toddler Zone Signs</title>
<link rel="stylesheet" href="https://fonts.googleapis.com/css2?family=Anton&family=Cabin:wght@600;700&family=Open+Sans:wght@400&display=swap">
<style>
  :root {
    --board: #e4e4e4;
    --label: #1a1a1a;
    --frame-yellow: #f3d21a;
    --frame-yellow-light: #f8e25a;
    --bamboo: #6f9e2a;
    --bamboo-dark: #4e7a1c;
    --panel-top: #eef3d6;
    --panel-mid: #fbf8e2;
    --panel-bottom: #fdfbea;
    --ink-green: #0d6a2e;
    --headline-green: #8cc63f;
    --headline-shadow: #3d6a14;
    --brand-grey: #5b5b5b;
    --accent-orange: #f39a1e;
    --foliage-dark: #2f6b1f;
    --foliage-light: #6ea532;
  }
  * { box-sizing: border-box; margin: 0; padding: 0; }
  html, body { width: 1200px; height: 884px; overflow: hidden; }
  body {
    background: var(--board);
    position: relative;
    font-family: "Cabin", sans-serif;
  }
  .sign-label {
    position: absolute;
    top: 64px;
    font-family: "Open Sans", sans-serif;
    font-size: 16px;
    color: var(--label);
  }
  .sign {
    position: absolute;
    top: 102px;
    width: 509px;
    height: 720px;
    background: repeating-linear-gradient(180deg, var(--frame-yellow) 0 24px, var(--frame-yellow-light) 24px 30px);
    box-shadow: 0 6px 10px rgba(0,0,0,0.25);
  }
  .sign--left { left: 56px; }
  .sign--right { left: 618px; }
  .sign__bamboo {
    position: absolute;
    inset: 18px;
    border: 5px solid var(--bamboo);
    outline: 1px solid var(--bamboo-dark);
  }
  .sign__panel {
    position: absolute;
    left: 24px; top: 24px; right: 24px; bottom: 24px;
    background: linear-gradient(180deg, var(--panel-top) 0%, var(--panel-mid) 35%, var(--panel-bottom) 100%);
    overflow: hidden;
  }
  .sign__foliage {
    position: absolute;
    left: 0; right: 0; bottom: 0;
    height: 62px;
    background: linear-gradient(180deg, var(--foliage-light) 0%, var(--foliage-dark) 100%);
    border-radius: 40% 40% 0 0 / 60% 60% 0 0;
  }
  .brand {
    position: absolute;
    left: 0; right: 0; top: 80px;
    text-align: center;
  }
  .brand__name {
    display: inline-flex;
    align-items: center;
    gap: 14px;
    font-family: "Cabin", sans-serif;
    font-weight: 700;
    font-size: 50px;
    line-height: 1;
    color: var(--ink-green);
    text-transform: uppercase;
  }
  .brand__dot {
    width: 38px; height: 38px;
    border-radius: 50%;
    background: var(--accent-orange);
  }
  .brand__tagline {
    margin-top: 12px;
    font-family: "Cabin", sans-serif;
    font-weight: 600;
    font-size: 24px;
    letter-spacing: 0.5px;
    color: var(--brand-grey);
  }
  .headline {
    position: absolute;
    left: 0; right: 0; top: 226px;
    text-align: center;
    font-family: "Anton", sans-serif;
    font-size: 72px;
    line-height: 1;
    color: var(--headline-green);
    text-shadow: 2px 3px 0 var(--headline-shadow);
  }
  .notice {
    position: absolute;
    left: 0; right: 0;
    text-align: center;
    font-weight: 600;
    color: var(--ink-green);
  }
  .notice--rules { top: 326px; font-size: 24px; line-height: 32px; }
  .notice--rules .gap { height: 32px; }
  .notice--details {
    top: 216px;
    left: 40px; right: 40px;
    font-size: 19.5px;
    line-height: 25.5px;
  }
  .notice--details p + p { margin-top: 25.5px; }
  .notice--details .thanks { margin-top: 50px; }
</style>
</head>
<body>

<div class="sign-label" style="left:80px">Toddler zone</div>
<div class="sign-label" style="left:619px">Toddler zone</div>

<section class="sign sign--left">
  <div class="sign__bamboo"></div>
  <div class="sign__panel">
    <div class="brand">
      <div class="brand__name">Pebble Hop <span class="brand__dot"></span></div>
      <div class="brand__tagline">MOBILE PLAY CENTRE</div>
    </div>
    <h1 class="headline">TODDLER ZONE</h1>
    <div class="notice notice--rules">
      <p>0-3 year olds ONLY</p>
      <p>Supervision required at all times</p>
      <div class="gap"></div>
      <p>Parents please wear socks too</p>
    </div>
    <div class="sign__foliage" role="img" aria-label="Row of jungle leaves and plants along the bottom edge"></div>
  </div>
</section>

<section class="sign sign--right">
  <div class="sign__bamboo"></div>
  <div class="sign__panel">
    <div class="brand">
      <div class="brand__name">Pebble Hop <span class="brand__dot"></span></div>
      <div class="brand__tagline">MOBILE PLAY CENTRE</div>
    </div>
    <div class="notice notice--details">
      <p>If using the toddler soft play equipment, please ensure that this area is used by children 0-3 ONLY.</p>
      <p>The equipment and ball pit is designed only for small children. Bigger kids might injure themselves, the smaller children or cause extensive damage to the equipment, of which there will be a charge back to the client.</p>
      <p class="thanks">Thank you.</p>
    </div>
    <div class="sign__foliage" role="img" aria-label="Row of jungle leaves and plants along the bottom edge"></div>
  </div>
</section>

</body>
</html>
```